Healthy Meal Delivery Website needs a new face lift

Hi there,

The current website i have is super old and outdated.

I would like a beautiful modern site that has all the same content as the previous except with a a new, modern and trustworthy feel.

The current website is http://www.larkibite.ca/

Target Market(s)

Diet Meal delivery, weight loss, healthy meal delivery

Industry/Entity Type

Food Service

Number of Pages Required

5+ page

Font styles to use
Sans Serif

Requirements
Must have
• Modern & Clean
Should not have
• Anything outdated or cheesy

```html
<!DOCTYPE html>
<html lang="en">
<head>
<meta charset="utf-8">
<title>Larkibite – Diet Meal Delivery</title>
<link href="https://fonts.googleapis.com/css2?family=Lato:ital,wght@0,400;0,700;0,900;1,400&family=Open+Sans:ital,wght@0,400;0,600;1,400&display=swap" rel="stylesheet">
<style>
:root{
  --blue:#29aee2;
  --blue-dark:#1f9fd3;
  --ink:#1d1d1f;
  --text:#555a60;
  --muted:#8a8f94;
  --light:#f1f1f1;
  --grey-band:#e4e4e4;
  --white:#ffffff;
  --footer-bar:#dadada;
}
*{margin:0;padding:0;box-sizing:border-box}
html,body{width:1200px;height:3147px;overflow:hidden}
body{position:relative;background:var(--white);font-family:"Open Sans",Arial,sans-serif;color:var(--text)}
.abs{position:absolute}
.heading{font-family:"Lato",Arial,sans-serif;font-weight:700;color:var(--ink);text-transform:uppercase}

/* header */
.site-header{position:absolute;left:0;top:0;width:1200px;height:130px;background:var(--white)}
.brand{position:absolute;left:150px;top:38px;display:flex;align-items:center;gap:12px;font-family:"Lato",sans-serif;font-weight:900;font-size:40px;color:var(--blue);letter-spacing:1px}
.brand-dot{width:22px;height:22px;border-radius:50%;background:var(--blue)}
.phone{position:absolute;left:797px;top:28px;display:flex;align-items:center;gap:8px;font-family:"Lato",sans-serif;font-weight:700;font-size:20px;color:var(--ink)}
.btn-outline{position:absolute;border:2px solid var(--blue);color:var(--blue);font-family:"Lato",sans-serif;font-weight:700;text-transform:uppercase;display:flex;align-items:center;justify-content:center;background:transparent}
.signup{left:965px;top:21px;width:99px;height:38px;font-size:14px}
.main-nav{position:absolute;left:400px;top:82px;display:flex;gap:36px;font-family:"Lato",sans-serif;font-weight:700;font-size:16px;color:#333}
.main-nav .active{color:var(--ink)}

/* hero */
.hero{position:absolute;left:0;top:130px;width:1200px;height:625px;background:linear-gradient(90deg,#f4f4f4,#ececec);overflow:hidden}
.hero-photo{position:absolute;left:520px;top:-40px;width:720px;height:640px;border-radius:50%;background:radial-gradient(circle at 50% 50%,#e0584a 0%,#f19a3e 22%,#5f9c2f 45%,#3f7a22 62%,#f6f6f6 64%,#e9e9e9 72%)}
.hero-title{position:absolute;left:117px;top:196px;font-family:"Lato",sans-serif;font-size:46px;line-height:54px;font-weight:700}
.hero-title .accent{color:var(--blue);display:block}
.hero-title .main{color:var(--ink);display:block}
.btn-dark{position:absolute;left:120px;top:319px;width:157px;height:40px;border:3px solid var(--ink);font-family:"Lato",sans-serif;font-weight:700;font-size:15px;color:var(--ink);display:flex;align-items:center;justify-content:center}
.slider-dots{position:absolute;display:flex;align-items:center;gap:6px}
.slider-dots .arrow{width:20px;height:20px;border-radius:50%;background:#555;color:#fff;font-size:11px;display:flex;align-items:center;justify-content:center}
.slider-dots .dot{width:9px;height:9px;border-radius:50%;background:#bbb}
.slider-dots .dot.on{background:#666}
.hero-wave{position:absolute;left:0;top:540px}

/* features */
.feature-plate{position:absolute;left:101px;top:804px;width:280px;height:280px;border-radius:50%;border:6px solid #e6e6e6;background:radial-gradient(circle,#d9433b 0%,#f0c53a 25%,#4f8f2c 50%,#2e6d1f 78%)}
.feature-arc{position:absolute;left:400px;top:690px}
.feature-icon{position:absolute;width:62px;height:62px;border-radius:50%;border:3px solid var(--blue);background:#fff;display:flex;align-items:center;justify-content:center}
.feature-label{position:absolute;width:260px;text-align:right}
.feature-label h4{font-family:"Lato",sans-serif;font-weight:700;font-size:16px;color:var(--ink)}
.feature-label p{font-size:12.5px;line-height:19px;color:var(--text)}
.intro{position:absolute;left:652px;top:818px;width:420px}
.intro h2{font-family:"Lato",sans-serif;font-weight:700;font-size:29px;line-height:34px;color:var(--ink)}
.intro p{margin-top:26px;font-size:14.5px;line-height:26px;color:var(--text)}
.read-more{left:655px;top:1081px;width:157px;height:41px;font-size:15px}

/* sample menu */
.menu-band{position:absolute;left:0;top:1227px;width:1200px;height:520px;background:var(--blue)}
.section-title-white{position:absolute;left:0;width:1200px;text-align:center;font-family:"Lato",sans-serif;font-weight:700;font-size:31px;color:#fff}
.menu-item{position:absolute;width:240px;text-align:center;color:#fff}
.menu-photo{width:188px;height:188px;margin:0 auto;clip-path:polygon(50% 0,65% 6%,82% 8%,88% 25%,100% 40%,96% 58%,100% 75%,84% 88%,70% 100%,50% 96%,30% 100%,16% 88%,0 75%,4% 58%,0 40%,12% 25%,18% 8%,35% 6%)}
.menu-item h3{margin-top:18px;font-family:"Lato",sans-serif;font-weight:700;font-size:23px}
.menu-item p{margin-top:6px;font-size:12.5px;line-height:19px}
.menu-wave{position:absolute;left:0;top:1640px}

/* programs */
.section-title{position:absolute;left:0;width:1200px;text-align:center;font-family:"Lato",sans-serif;font-weight:700;font-size:31px;color:var(--ink)}
.program-card{position:absolute;top:1857px;width:432px;height:365px;border:1px solid #dcdcdc;background:#fff;text-align:center}
.program-photo{height:220px}
.program-card h3{margin-top:14px;font-family:"Lato",sans-serif;font-weight:700;font-size:21px;color:var(--blue)}
.program-card p{margin:8px auto 0;width:380px;font-size:12.5px;line-height:19px;color:var(--text)}
.program-card .more{display:block;margin-top:10px;font-family:"Lato",sans-serif;font-weight:700;font-size:12.5px;color:var(--ink)}
.program-card .more span{color:var(--blue)}
.card-edge{position:absolute;top:1857px;height:365px;border:1px solid #dcdcdc;background:#f3f3f3}
.carousel-arrow{position:absolute;top:2012px}

/* testimonials */
.testimonial-band{position:absolute;left:0;top:2290px;width:1200px;height:520px}
.person-photo{position:absolute;left:126px;top:2392px;width:336px;height:398px;background:radial-gradient(ellipse at 50% 60%,#f3f3f3 0%,#dcdcdc 55%,#d2d2d2 100%)}
.testimonial h2{position:absolute;left:508px;top:2414px;font-family:"Lato",sans-serif;font-weight:700;font-size:27px;color:var(--ink)}
.quote{position:absolute;left:545px;top:2498px;width:470px;font-style:italic;font-size:17px;line-height:33px;color:#666}
.qmark{position:absolute;font-family:"Lato",sans-serif;font-weight:900;font-size:56px;color:var(--blue);line-height:1}
.author{position:absolute;left:545px;top:2614px;font-family:"Lato",sans-serif;font-weight:700;font-size:18px;color:var(--ink)}

/* footer */
.site-footer{position:absolute;left:0;top:2790px;width:1200px;height:290px;background:#fff}
.footer-heading{position:absolute;font-family:"Lato",sans-serif;font-weight:700;font-size:15px;color:var(--ink);text-transform:uppercase}
.field{position:absolute;left:122px;width:293px;height:38px;border:1px solid #999;font-size:13px;color:#444;padding-left:16px;display:flex;align-items:center}
.btn-send{position:absolute;left:122px;top:2994px;width:105px;height:34px;background:var(--blue);color:#fff;font-family:"Lato",sans-serif;font-weight:700;font-size:15px;display:flex;align-items:center;justify-content:center}
.footer-divider{position:absolute;left:453px;top:2848px;width:1px;height:172px;background:#999}
.footer-links{position:absolute;list-style:none;font-size:14px;line-height:29.5px;color:#333}
.footer-contact{position:absolute;left:860px;top:2890px;font-size:14px;line-height:22px;color:#333}
.social{position:absolute;top:2943px;width:38px;height:38px;border-radius:50%;border:2px solid var(--blue)}
.copyright-bar{position:absolute;left:0;top:3080px;width:1200px;height:67px;background:var(--footer-bar);display:flex;align-items:center;justify-content:center;font-size:13px;color:#444}
</style>
</head>
<body>

<header class="site-header">
  <div class="brand"><span class="brand-dot"></span>LARKIBITE</div>
  <div class="phone">
    <svg width="20" height="20" viewBox="0 0 24 24"><path fill="#29aee2" d="M6.6 10.8a15 15 0 0 0 6.6 6.6l2.2-2.2c.3-.3.7-.4 1-.2 1.1.4 2.3.6 3.6.6.6 0 1 .4 1 1V20c0 .6-.4 1-1 1A17 17 0 0 1 3 4c0-.6.4-1 1-1h3.5c.6 0 1 .4 1 1 0 1.3.2 2.5.6 3.6.1.3 0 .7-.2 1z"/></svg>
    416-555-0142
  </div>
  <div class="btn-outline signup">Sign up</div>
  <nav class="main-nav">
    <span class="active">HOME</span><span>HOW IT WORKS</span><span>PRICING</span><span>MENU</span><span>CELEBRITY</span><span>FAQ</span><span>CONTACT</span>
  </nav>
</header>

<section class="hero">
  <div class="hero-photo" role="img" aria-label="Bowl of fresh salad with spinach, orange, grapefruit and pomegranate"></div>
  <h1 class="hero-title"><span class="accent">GREAT TASTING</span><span class="main">DIET MEAL DELIVERY</span></h1>
  <div class="btn-dark">VIEW MEAL</div>
  <div class="slider-dots" style="left:117px;top:391px">
    <span class="arrow">‹</span><span class="dot on"></span><span class="dot"></span><span class="dot"></span><span class="dot"></span><span class="arrow">›</span>
  </div>
  <svg class="hero-wave" width="1200" height="90" viewBox="0 0 1200 90"><path d="M0 40 C300 90 800 -10 1200 60 L1200 90 L0 90Z" fill="#fff"/></svg>
</section>

<section class="features">
  <div class="feature-plate" role="img" aria-label="Plate of mixed salad with tomatoes, olives and peppers"></div>
  <svg class="feature-arc" width="220" height="540" viewBox="0 0 220 540"><path d="M40 0 Q260 270 20 540" fill="none" stroke="#555" stroke-width="2" stroke-dasharray="3 6"/></svg>

  <div class="feature-icon" style="left:504px;top:747px"><svg width="26" height="30" viewBox="0 0 26 30"><rect x="2" y="2" width="22" height="26" rx="2" fill="none" stroke="#29aee2" stroke-width="2.5"/><path d="M9 8v14M17 8v14" stroke="#29aee2" stroke-width="2.5"/></svg></div>
  <div class="feature-icon" style="left:552px;top:865px"><svg width="30" height="30" viewBox="0 0 30 30"><circle cx="15" cy="15" r="12" fill="none" stroke="#29aee2" stroke-width="2.5"/><circle cx="15" cy="15" r="6" fill="none" stroke="#29aee2" stroke-width="2.5"/></svg></div>
  <div class="feature-icon" style="left:552px;top:987px"><svg width="30" height="28" viewBox="0 0 30 28"><path d="M15 25 L4 14 A6 6 0 0 1 15 6 A6 6 0 0 1 26 14Z" fill="none" stroke="#29aee2" stroke-width="2.5"/></svg></div>
  <div class="feature-icon" style="left:504px;top:1102px"><svg width="32" height="24" viewBox="0 0 32 24"><rect x="1" y="3" width="19" height="14" fill="#29aee2"/><path d="M20 7h6l5 5v5H20z" fill="#29aee2"/><circle cx="8" cy="20" r="3" fill="#29aee2"/><circle cx="25" cy="20" r="3" fill="#29aee2"/></svg></div>

  <div class="feature-label" style="left:233px;top:762px"><h4>VARIETY</h4><p>60 Day Menu Rotation</p></div>
  <div class="feature-label" style="left:285px;top:866px"><h4>MENU</h4><p>Inspired fresh gourmet<br>Larkibite diet meals</p></div>
  <div class="feature-label" style="left:285px;top:984px"><h4>BENEFITS</h4><p>Fresh diet meal<br>delivery daily</p></div>
  <div class="feature-label" style="left:233px;top:1101px"><h4>DELIVERY</h4><p>Fresh diet meal delivery daily<br>Toronto and Canada wide</p></div>

  <div class="intro">
    <h2>FRESH DIET GOURMET MEALS DELIVERED BY LARKIBITE</h2>
    <p>Fresh diet meal delivery Toronto and Canada wide is our signature fresh gourmet diet meal delivery program designed for healthy living &amp; weight loss management. Diet meal delivery Toronto has a creative gourmet menu that uses exotic flavors and ingredients to enhance your dining experience</p>
  </div>
  <div class="btn-outline read-more">READ MORE</div>
</section>

<section class="menu-band">
  <h2 class="section-title-white" style="top:42px">SAMPLE MENU</h2>
  <div class="menu-item" style="left:100px;top:112px">
    <div class="menu-photo" role="img" aria-label="Breakfast wraps" style="background:radial-gradient(circle,#c98a5a,#8a4a2c 70%,#5a2e1e)"></div>
    <h3>BREAKFAST</h3><p>Morbi diam mauris viverra in<br>gravida eu mattis ante</p>
  </div>
  <div class="menu-item" style="left:354px;top:112px">
    <div class="menu-photo" role="img" aria-label="Lunch plate of roasted vegetables and greens" style="background:radial-gradient(circle,#8a5a3a,#4a6a2a 60%,#2e3e1e)"></div>
    <h3>LUNCH</h3><p>Morbi diam mauris viverra in<br>gravida eu mattis ante</p>
  </div>
  <div class="menu-item" style="left:608px;top:112px">
    <div class="menu-photo" role="img" aria-label="Glazed chicken snacks" style="background:radial-gradient(circle,#a04a30,#7a2e20 60%,#4a1e16)"></div>
    <h3>SNACKS</h3><p>Morbi diam mauris viverra in<br>gravida eu mattis ante</p>
  </div>
  <div class="menu-item" style="left:862px;top:112px">
    <div class="menu-photo" role="img" aria-label="Dinner of beef and greens" style="background:radial-gradient(circle,#6a3a2a,#3e5a24 60%,#24301a)"></div>
    <h3>DINNER</h3><p>Morbi diam mauris viverra in<br>gravida eu mattis ante</p>
  </div>
</section>
<svg class="menu-wave" width="1200" height="110" viewBox="0 0 1200 110">
  <path d="M0 30 C350 90 800 20 1200 60 L1200 110 L0 110Z" fill="#fff"/>
  <path d="M0 24 C300 60 600 40 780 28" fill="none" stroke="#fff" stroke-width="6"/>
</svg>

<section class="programs">
  <h2 class="section-title" style="top:1785px">OUR PROGRAMS</h2>
  <div class="card-edge" style="left:0;width:63px"></div>
  <div class="card-edge" style="left:1148px;width:60px"></div>
  <svg class="carousel-arrow" style="left:80px" width="24" height="58" viewBox="0 0 24 58"><path d="M22 2 L3 29 L22 56" fill="none" stroke="#444" stroke-width="2"/></svg>
  <svg class="carousel-arrow" style="left:1106px" width="24" height="58" viewBox="0 0 24 58"><path d="M2 2 L21 29 L2 56" fill="none" stroke="#444" stroke-width="2"/></svg>

  <article class="program-card" style="left:155px">
    <div class="program-photo" role="img" aria-label="Grilled flatbread with vegetables and salad" style="background:linear-gradient(135deg,#6f9a3a,#c9a06a 50%,#8a5a30)"></div>
    <h3>Program Title here</h3>
    <p>Morbi diam mauris viverra in gravida eu mattis in ante Morbi eget arcu Morbi porta libero id ullamcorper nonummy</p>
    <span class="more">READ MORE <span>›</span></span>
  </article>
  <article class="program-card" style="left:613px">
    <div class="program-photo" role="img" aria-label="Woman eating a healthy meal at a kitchen table" style="background:linear-gradient(135deg,#cfc7b8,#9fb27a 55%,#6f8a4a)"></div>
    <h3>Program Title here</h3>
    <p>Morbi diam mauris viverra in gravida eu mattis in ante Morbi eget arcu Morbi porta libero id ullamcorper nonummy</p>
    <span class="more">READ MORE <span>›</span></span>
  </article>
</section>

<section class="testimonial">
  <svg class="testimonial-band" width="1200" height="520" viewBox="0 0 1200 520">
    <path d="M0 20 C300 70 700 80 1200 10 L1200 485 L1150 492 L1080 482 L1000 494 L900 484 L800 495 L700 486 L600 494 L500 483 L400 492 L300 485 L200 495 L100 486 L0 493Z" fill="#e8e8e8"/>
    <path d="M500 40 C800 50 1000 30 1200 0" fill="none" stroke="#fff" stroke-width="8"/>
  </svg>
  <div class="person-photo" role="img" aria-label="Smiling woman showing weight loss in oversized jeans"></div>
  <h2>TESTIMONIALS</h2>
  <span class="qmark" style="left:490px;top:2484px">“</span>
  <p class="quote">Morbi diam mauris viverra in gravida eu mattis in ante Morbi eget arcu Morbi porta libero id ullamcorper nonummy nibh ligula pulvinara metus eget</p>
  <span class="qmark" style="left:900px;top:2556px">”</span>
  <div class="author">By Author Name</div>
  <div class="slider-dots" style="left:545px;top:2676px">
    <span class="arrow">‹</span><span class="dot on"></span><span class="dot"></span><span class="dot"></span><span class="dot"></span><span class="arrow">›</span>
  </div>
</section>

<footer class="site-footer">
  <h4 class="footer-heading" style="left:122px;top:64px">CONTACT US</h4>
  <div class="footer-heading" style="left:525px;top:64px">COMPANY</div>
  <div class="footer-heading" style="left:684px;top:64px">RESOURCES</div>
  <div class="footer-heading" style="left:860px;top:64px">CONTACT US</div>
</footer>
<div class="field" style="top:2891px">Your Name</div>
<div class="field" style="top:2939px">Email address</div>
<div class="btn-send">SEND</div>
<div class="footer-divider"></div>
<ul class="footer-links" style="left:525px;top:2890px"><li>Home</li><li>About Us</li><li>Pricing</li><li>How it Works</li></ul>
<ul class="footer-links" style="left:684px;top:2890px"><li>Sample Menu</li><li>Celebrity</li><li>FAQ</li><li>Contact Us</li></ul>
<div class="footer-contact">Contact Us now at:<br>hello@larkibite.ca</div>
<span class="social" style="left:862px"></span>
<span class="social" style="left:904px"></span>
<span class="social" style="left:946px"></span>
<span class="social" style="left:988px"></span>

<div class="copyright-bar">© 2018 Company Name &nbsp;All right reserved</div>

</body>
</html>
```